Bright Harbor, LLC Business Card Design

We need a product business card designed for a new company Bright Harbor, LLC. We make and resell waterless RV cleaner, polish and protectant. It cleans and protects in a simple spray and wipe step leaving the surface protected and conditioned to repel dust, dirt, water, smudges, bugs and fingerprints while preventing fogging. Safe on acrylic, plexiglas, lexan, plastic, rubber, painted surfaces, chrome, stainless, aluminum, vinyl, leather, glass.... This is an eco-friendly green product.

We want to play off the company name to tell the consumer that the product is easy to use and associate to the nostalgics 1950's in the USA... Thinking old travel trailer with hot rod truck pulling it as the graphic, maybe the husband cleaning the truck and the wife cleaning the trailer for a Bright Harbor surface.
Updates

Just posted our newly finished logo. Need to have "Cleaner and Protectant" added to the design as well. Thanks everyone that has submitted thus far, i am working to get comments on all.

If you need a different file format, please let me know. Thank you.

Most important info, is the logo, website and the words "Cleaner" or "Clean" along "Protectant" or "Protect" the remainder is of less importance. Highlight: www.brightharborwash.example Focus is on company brand for Brighter Harbor Cleaner product: However, need a section for the following contact info: Walt Ferris (xxx) xxx-xxxx email address Would like space for QR Code if possible.

Target Market(s)

Adults in the USA between ages of 35-75 that are actively involved in the Recreational Vehicle (RV), travel trailer, and hot rod lifestyle. We are targeting the RV marked of the high end travel, 5th wheel and bus RV market. Along with hot rods, automotive and motorcycle market.

Industry/Entity Type

Travel

Requirements
Must have
• Most important info, is the logo, website and the words "Cleaner" or "Clean" along "Protectant" or "Protect" the remainder is of less importance.

Highlight:
www.brightharborwash.example

Focus is on company brand for Brighter Harbor Cleaner product: However, need a section for the following contact info:

Walt Ferris
(xxx) xxx-xxxx
email address
Nice to have
• Would like a space for a QR Code.

```html
<!DOCTYPE html>
<html lang="en">
<head>
<meta charset="utf-8">
<title>Bright Harbor, LLC – Business Card</title>
<link rel="stylesheet" href="https://fonts.googleapis.com/css2?family=Aldrich&display=swap">
<style>
  :root {
    --page-bg: #e9ebee;
    --card-white: #ffffff;
    --card-shade: #f1f2f4;
    --blue-deep: #2f4fb8;
    --blue-bright: #1a9be3;
    --swoosh-dark: #2b2c30;
    --swoosh-mid: #8a8c92;
    --ink-dark: #1c1d22;
    --ink-soft: #5a5d66;
    --ink-light: #ffffff;
  }
  * { margin: 0; padding: 0; box-sizing: border-box; }
  html, body {
    width: 1200px; height: 900px; overflow: hidden;
    background: var(--page-bg);
  }
  .canvas {
    position: relative; width: 1200px; height: 900px;
    display: flex; align-items: center; justify-content: center;
  }
  .business-card {
    position: relative; width: 1000px; height: 600px;
    border-radius: 52px; overflow: hidden;
    background: var(--card-white);
    box-shadow: 0 18px 40px rgba(20, 30, 60, 0.18);
    font-family: "Aldrich", sans-serif;
  }
  .card-shapes { position: absolute; inset: 0; width: 100%; height: 100%; }
  .brand {
    position: absolute; top: 96px; right: 90px; text-align: right;
  }
  .brand-name {
    font-size: 74px; letter-spacing: 1px;
    color: var(--ink-dark); text-transform: uppercase;
    font-weight: 400; line-height: 1;
  }
  .brand-tagline {
    margin-top: 12px; font-size: 22px; letter-spacing: 4px;
    color: var(--ink-soft); text-transform: uppercase;
  }
  .holder {
    position: absolute; left: 62px; top: 292px; color: var(--ink-light);
  }
  .holder-name { font-size: 30px; letter-spacing: 1.5px; text-transform: uppercase; }
  .holder-role { font-size: 20px; margin-top: 6px; }
  .holder-address {
    position: absolute; left: 62px; top: 398px;
    color: var(--ink-light); font-size: 22px; line-height: 1.4;
    font-style: normal;
  }
  .contact-list {
    position: absolute; right: 44px; top: 420px;
    list-style: none; color: var(--ink-light); font-size: 20px;
  }
  .contact-item {
    display: flex; align-items: center; justify-content: flex-end;
    gap: 14px; height: 32px; letter-spacing: 1px;
  }
  .contact-icon { width: 22px; height: 22px; flex: none; }
</style>
</head>
<body>
<main class="canvas">
  <article class="business-card">
    <svg class="card-shapes" viewBox="0 0 1000 600" preserveAspectRatio="none" aria-hidden="true">
      <defs>
        <linearGradient id="blueBand" x1="0" y1="0" x2="1" y2="0.4">
          <stop offset="0" stop-color="#2f4fb8"/>
          <stop offset="1" stop-color="#1a9be3"/>
        </linearGradient>
        <linearGradient id="whiteFade" x1="0" y1="0" x2="0" y2="1">
          <stop offset="0" stop-color="#f1f2f4"/>
          <stop offset="0.5" stop-color="#ffffff"/>
        </linearGradient>
      </defs>
      <rect class="top-field" width="1000" height="600" fill="url(#whiteFade)"/>
      <path class="swoosh-dark" d="M0,190 C260,160 520,240 680,300 C800,345 900,345 1000,330 L1000,355 C900,368 800,370 680,325 C520,265 260,200 0,225 Z" fill="var(--swoosh-dark)"/>
      <path class="swoosh-mid" d="M0,215 C260,190 520,262 680,322 C800,367 900,365 1000,350 L1000,370 C900,382 800,385 680,340 C520,282 260,222 0,245 Z" fill="var(--swoosh-mid)"/>
      <path class="swoosh-light" d="M0,238 C260,214 520,282 680,342 C800,388 900,384 1000,370 L1000,385 C900,398 800,402 680,358 C520,298 260,230 0,250 Z" fill="var(--card-white)"/>
      <path class="blue-band" d="M0,250 C260,230 520,298 680,356 C800,400 900,398 1000,383 L1000,600 L0,600 Z" fill="url(#blueBand)"/>
    </svg>

    <header class="brand">
      <h1 class="brand-name">Bright Harbor</h1>
      <p class="brand-tagline">Cleaner and Protectant</p>
    </header>

    <section class="holder">
      <p class="holder-name">Walt Ferris</p>
      <p class="holder-role">Managing Director</p>
    </section>
    <address class="holder-address">214, 6th floor, Dock<br>Lane Road BHV</address>

    <ul class="contact-list">
      <li class="contact-item">012 555 0147
        <svg class="contact-icon" viewBox="0 0 24 24" aria-hidden="true"><path d="M6.6 3.5l3 3.2-1.8 2.2c1.2 2.6 3.1 4.6 5.7 5.8l2.2-1.8 3.2 3-1.8 3.1C10.8 19.5 4.5 13.2 3.5 5.3z" fill="currentColor"/></svg>
      </li>
      <li class="contact-item">012 555 0148
        <svg class="contact-icon" viewBox="0 0 24 24" aria-hidden="true"><rect x="7" y="2.5" width="10" height="19" rx="2" fill="none" stroke="currentColor" stroke-width="2"/><circle cx="12" cy="18" r="1.2" fill="currentColor"/></svg>
      </li>
      <li class="contact-item">012 555 0149
        <svg class="contact-icon" viewBox="0 0 24 24" aria-hidden="true"><rect x="4" y="9" width="16" height="11" rx="1.5" fill="currentColor"/><rect x="7" y="3" width="10" height="7" fill="none" stroke="currentColor" stroke-width="2"/></svg>
      </li>
      <li class="contact-item">walt@brightharbor.example
        <svg class="contact-icon" viewBox="0 0 24 24" aria-hidden="true"><rect x="3" y="6" width="18" height="13" rx="1.5" fill="currentColor"/><path d="M3.5 7l8.5 6.5L20.5 7" fill="none" stroke="#1a9be3" stroke-width="1.6"/></svg>
      </li>
      <li class="contact-item">www.brightharborwash.example
        <svg class="contact-icon" viewBox="0 0 24 24" aria-hidden="true"><circle cx="12" cy="12" r="9" fill="none" stroke="currentColor" stroke-width="2"/><ellipse cx="12" cy="12" rx="4" ry="9" fill="none" stroke="currentColor" stroke-width="1.6"/><path d="M3 12h18" stroke="currentColor" stroke-width="1.6"/></svg>
      </li>
    </ul>
  </article>
</main>
</body>
</html>
```